Business Card Design - Photographer

I am a landscape photographer and I require a business card design. 

I require two designs:
1)  a double sided business card
 and
b)  a single sided business card 

The single sided design can either be the same as the double sided (with just one side having all the information)....or it can be an entire new design. Its up to you.

My corporate colours are (CMYK):

Blue   69, 32, 0, 0
Grey  72,  64,  47,  31
Green  32,  2,  91,  0
Yellow   0, 19, 92, 0
Orange  0, 39, 75, 0

Colour space in final file should be in CMYK.

The details that need to be included on the card:

- Use the provided Logo
- Name: Wiktor Baranowski
- Email:   sales@vistalumeworks.com.au
- Website:    vistalumeworks.com.au
- Twitter:    twitter.com/vistalumeworks
- Facebook:   facebook.com/vistalumeworks
- Mobile  0417 539 662

Please use the attached template to design the logo to the specified size, including the marked bleed lines. I have also attached my logo in PNG (transparent background) and ai format for you to use.

The final file should be:
- Photoshop version with layers so I can edit the name/text etc. All non vector files should be high resolution at 1039 x 697 pixels at 300 dpi.

I also require a file as:
- Vector based PDF

Anyway questions please contact me.

Thank you

Industry/Entity Type

Landscape

Logo styles of interest
Pictorial/Combination Logo
Abstract Logo
Wordmark Logo
Lettermark Logo
Requirements
Must have
• The details that need to be included on the card:

- Use the provided Logo
- Name: Wiktor Baranowski
- Email: sales@vistalumeworks.com.au
- Website: vistalumeworks.com.au
- Twitter: twitter.com/vistalumeworks
- Facebook: facebook.com/vistalumeworks
- Mobile 0417 539 662

```html
<!DOCTYPE html>
<html lang="en">
<head>
<meta charset="utf-8">
<title>Vistalume Works – Business Cards</title>
<link href="https://fonts.googleapis.com/css2?family=Tinos:wght@400;700&display=swap" rel="stylesheet">
<style>
  :root {
    --backdrop: #e9e6e1;
    --card: #ffffff;
    --card-edge: #bdbab5;
    --brand-grey: #3d4152;
    --ink: #4a4a4a;
    --rule-grey: #c9c9c9;
    --brand-blue: #4a8ec8;
    --social: #5aa6d8;
  }
  * { margin: 0; padding: 0; box-sizing: border-box; }
  html, body { width: 1200px; height: 1085px; overflow: hidden; }
  body {
    background: var(--backdrop);
    position: relative;
    font-family: "Tinos", "Times New Roman", serif;
    color: var(--ink);
  }
  .card {
    position: absolute;
    width: 773px;
    height: 441px;
    background: var(--card);
    border: 1px solid var(--card-edge);
  }
  .card--front { left: 72px; top: 62px; }
  .card--back  { left: 355px; top: 554px; }

  .brand { position: absolute; text-align: center; }
  .brand__mark {
    display: block;
    margin: 0 auto;
    border-radius: 50%;
    background: var(--brand-grey);
  }
  .brand__name {
    display: block;
    color: var(--brand-grey);
    font-weight: 400;
    text-transform: uppercase;
    white-space: nowrap;
    line-height: 1;
  }
  .brand__rule {
    display: block;
    height: 2px;
    background: var(--brand-grey);
  }
  .brand__tagline {
    display: block;
    color: var(--brand-grey);
    font-weight: 700;
    text-transform: uppercase;
    white-space: nowrap;
    line-height: 1;
  }

  /* front card brand block */
  .card--front .brand { left: 25px; top: 91px; width: 350px; }
  .card--front .brand__mark { width: 126px; height: 126px; }
  .card--front .brand__name { margin-top: 24px; font-size: 32px; letter-spacing: 0.5px; }
  .card--front .brand__rule { margin-top: 4px; }
  .card--front .brand__tagline { margin-top: 7px; font-size: 14px; letter-spacing: 2.2px; }

  /* back card brand block */
  .card--back .brand { left: 176px; top: 71px; width: 423px; }
  .card--back .brand__mark { width: 132px; height: 132px; }
  .card--back .brand__name { margin-top: 45px; font-size: 38px; letter-spacing: 1px; }
  .card--back .brand__rule { margin-top: 5px; }
  .card--back .brand__tagline { margin-top: 11px; font-size: 16px; letter-spacing: 2.6px; }

  .divider {
    position: absolute;
    left: 405px; top: 100px;
    width: 2px; height: 199px;
    background: var(--rule-grey);
  }
  .contact {
    position: absolute;
    left: 432px; top: 113px;
    list-style: none;
    font-size: 19px;
    line-height: 27px;
  }
  .contact__address { margin-bottom: 17px; }
  .contact__item { display: flex; align-items: center; gap: 8px; }
  .contact__icon { width: 13px; height: 13px; flex: none; fill: var(--ink); }
  .contact__social { width: 13px; height: 13px; flex: none; background: var(--social); border-radius: 2px; }

  .band { position: absolute; top: 363px; height: 4px; }
  .band--grey { left: 0; width: 37px; background: var(--brand-grey); }
  .band--blue { left: 46px; right: 0; background: var(--brand-blue); }

  .website {
    position: absolute;
    left: 0; right: 0;
    text-align: center;
    letter-spacing: 3px;
    color: var(--ink);
  }
  .card--front .website { top: 394px; font-size: 21px; padding-right: 12px; }
  .card--back .website { top: 375px; font-size: 20px; }
</style>
</head>
<body>

<section class="card card--front" aria-label="Business card front">
  <div class="brand">
    <span class="brand__mark"></span>
    <span class="brand__name">Vistalume Works</span>
    <span class="brand__rule"></span>
    <span class="brand__tagline">Fine Art Photography</span>
  </div>

  <div class="divider"></div>

  <ul class="contact">
    <li class="contact__address">00, Complex Name<br>State Name, City 0020</li>
    <li class="contact__item">
      <svg class="contact__icon" viewBox="0 0 10 14" aria-hidden="true"><rect x="1" y="0" width="8" height="14" rx="1.5"/><rect x="2.5" y="2" width="5" height="7" fill="#fff"/><circle cx="5" cy="11.5" r="1" fill="#fff"/></svg>
      0417 539 662
    </li>
    <li class="contact__item"><span class="contact__social"></span>vistalumeworks</li>
    <li class="contact__item"><span class="contact__social"></span>vistalumeworks</li>
    <li class="contact__item">
      <svg class="contact__icon" viewBox="0 0 14 10" aria-hidden="true"><rect x="0" y="0" width="14" height="10" rx="1"/><path d="M1 1 L7 6 L13 1" fill="none" stroke="#fff" stroke-width="1.2"/></svg>
      sales@vistalumeworks.com.au
    </li>
  </ul>

  <div class="band band--grey"></div>
  <div class="band band--blue"></div>

  <p class="website">www.vistalumeworks.com.au</p>
</section>

<section class="card card--back" aria-label="Business card back">
  <div class="brand">
    <span class="brand__mark"></span>
    <span class="brand__name">Vistalume Works</span>
    <span class="brand__rule"></span>
    <span class="brand__tagline">Fine Art Photography</span>
  </div>
  <p class="website">www.vistalumeworks.com.au</p>
</section>

</body>
</html>
```